Flat Belly Design Graphics for Social

I want to create 9 social media graphics (new Instagram size 4:5 (1080 x 1350 pixels) focusing on our Flat Belly Graphics, using the pics attached. Use the attached pics, NO RANDOM STOCK PHOTOGRAPHY. For the color scheme of the graphics, the color palette is attached. YOU MUST POST ALL 9 GRAPHICS IN ONE ENTRY.
Using the 3 titles below, create one set of graphics. 1) with all text, then for the others, use the pictures as detailed below in IMPORTANT:
1. Ten-Week Bright Morning Reboot
2. The Quick Garden Kitchen Menu Guide
3. Studio Habits for Lasting Energy Past Midlife - Zero Gym Needed
IMPORTANT:
Only use RK Pic 1 and RK Pic 2 with the title, Ten-Week Bright Morning Reboot
Only use meal plan1 and meal plan2 pics with the title, Quick Garden Kitchen Menu Guide
Only use studio habits 1 and studio habits 2 pics with the title, Studio Habits for Lasting Energy Past Midlife - Zero Gym Needed
women over 40

```html
<!DOCTYPE html>
<html lang="en">
<head>
<meta charset="utf-8">
<title>Social Graphics Set</title>
<link href="https://fonts.googleapis.com/css2?family=Oswald:wght@500;600;700&display=swap" rel="stylesheet">
<style>
  :root{
    --backdrop:#1f0008;
    --blush:#fbeeee;
    --blush-deep:#fde6ec;
    --forest:#2f4f4a;
    --rose:#e096ad;
    --white:#ffffff;
  }
  *{margin:0;padding:0;box-sizing:border-box}
  html,body{width:1085px;height:1200px;overflow:hidden;background:var(--backdrop)}
  body{position:relative;font-family:"Oswald",sans-serif}
  .tile{position:absolute;width:217px;height:272px;overflow:hidden;background:var(--blush)}
  .col-1{left:201px}.col-2{left:433px}.col-3{left:666px}
  .row-1{top:177px}.row-2{top:464px}.row-3{top:752px}
  .photo{position:absolute;left:0;width:100%}
  .overlay{position:absolute;inset:0;width:100%;height:100%}
  .caption{position:absolute;left:0;right:0;text-align:center;text-transform:uppercase;line-height:1}
  .caption span,.stack span{display:block;white-space:nowrap}
  .rose{color:var(--rose)}
  .forest{color:var(--forest)}
  .white{color:var(--white)}

  .stack{position:absolute;inset:0;display:flex;flex-direction:column;line-height:.98}
  .stack.center{align-items:center;text-align:center;justify-content:center}
  .stack.left{padding-left:21px}
  .pill{margin-top:8px;background:var(--rose);color:var(--white);border-radius:22px;width:194px;height:42px;display:flex !important;align-items:center;justify-content:center;font-size:30px;font-weight:600}
  .caption .tag{display:inline-block;padding:3px 10px;line-height:1;color:var(--white)}
  .tag-rose{background:var(--rose)}
  .tag-forest{background:var(--forest)}

  .tone-portrait{background:linear-gradient(180deg,#f7ecec 0%,#f1e4e4 60%,#e8dada 100%)}
  .tone-kitchen{background:linear-gradient(180deg,#6b4a35 0%,#a98a72 50%,#d8cfc8 100%)}
  .tone-food{background:radial-gradient(circle at 30% 30%,#f3c8b0 0%,#b24b3a 30%,#5a3b28 70%,#3e2a1d 100%)}
  .tone-produce{background:radial-gradient(circle at 50% 50%,#3a2e28 0%,#4b3a2f 40%,#7a8a3a 70%,#c9503a 100%)}
  .tone-sky{background:linear-gradient(180deg,#7fd0e4 0%,#5ab6d0 100%)}
  .tone-light{background:linear-gradient(180deg,#f4f2f0 0%,#c79e86 50%,#e9e4e1 100%)}
</style>
</head>
<body>

<section class="tile col-1 row-1">
  <div class="stack center">
    <span class="rose" style="font-size:40px;font-weight:600">TEN-WEEK</span>
    <span class="forest" style="font-size:48px;font-weight:600">Bright</span>
    <span class="forest" style="font-size:48px;font-weight:600">Morning</span>
    <span class="pill">REBOOT</span>
  </div>
</section>

<section class="tile col-2 row-1">
  <div class="stack left" style="padding-top:36px">
    <span class="rose" style="font-size:31px;font-weight:600">QUICK</span>
    <span class="forest" style="font-size:58px;font-weight:700">Garden</span>
    <span class="forest" style="font-size:58px;font-weight:700">Kitchen</span>
    <span class="rose" style="font-size:34px;font-weight:600;margin-top:10px">MENU GUIDE</span>
  </div>
</section>

<section class="tile col-3 row-1">
  <div class="stack left" style="padding-top:44px">
    <span class="rose" style="font-size:32px;font-weight:600">STUDIO</span>
    <span class="rose" style="font-size:32px;font-weight:600">HABITS FOR</span>
    <span class="forest" style="font-size:30px;font-weight:600;margin-top:6px">Lasting Energy</span>
    <span class="forest" style="font-size:30px;font-weight:600">Past Midlife</span>
    <span class="rose" style="font-size:22px;font-weight:600;margin-top:6px">ZERO GYM NEEDED</span>
  </div>
</section>

<section class="tile col-1 row-2">
  <div class="photo tone-portrait" style="top:0;height:170px" role="img" aria-label="Smiling woman in a white cropped sweater pointing at her waist"></div>
  <svg class="overlay" viewBox="0 0 217 272" preserveAspectRatio="none" aria-hidden="true">
    <polygon points="0,160 108.5,136 217,160 217,272 0,272" fill="var(--rose)"/>
    <polygon points="0,167 108.5,143 217,167 217,272 0,272" fill="var(--forest)"/>
  </svg>
  <div class="caption" style="top:171px">
    <span class="white" style="font-size:33px;font-weight:700">TEN-WEEK</span>
    <span class="white" style="font-size:26px;font-weight:700">BRIGHT MORNING</span>
    <span class="rose" style="font-size:24px;font-weight:500;margin-top:4px">REBOOT</span>
  </div>
</section>

<section class="tile col-2 row-2">
  <div class="photo tone-food" style="top:0;height:160px" role="img" aria-label="Healthy ingredients around a menu notepad on a wooden table"></div>
  <svg class="overlay" viewBox="0 0 217 272" preserveAspectRatio="none" aria-hidden="true">
    <polygon points="0,145 108.5,122 217,145 217,272 0,272" fill="var(--rose)"/>
    <polygon points="0,151 108.5,129 217,151 217,272 0,272" fill="var(--blush)"/>
  </svg>
  <div class="caption" style="top:165px">
    <span class="forest" style="font-size:32px;font-weight:500">QUICK GARDEN</span>
    <span class="forest" style="font-size:32px;font-weight:500;margin-top:2px">KITCHEN</span>
    <span class="rose" style="font-size:24px;font-weight:500;margin-top:4px">MENU GUIDE</span>
  </div>
</section>

<section class="tile col-3 row-2">
  <div class="photo tone-sky" style="top:105px;height:167px" role="img" aria-label="Two women sharing a secret against a blue backdrop"></div>
  <svg class="overlay" viewBox="0 0 217 272" preserveAspectRatio="none" aria-hidden="true">
    <polygon points="0,0 217,0 217,112 108.5,138 0,112" fill="var(--forest)"/>
    <polygon points="0,0 217,0 217,106 108.5,132 0,106" fill="var(--blush)"/>
  </svg>
  <div class="caption" style="top:12px">
    <span class="forest" style="font-size:20px;font-weight:500">STUDIO HABITS FOR</span>
    <span class="forest" style="font-size:20px;font-weight:500;margin-top:2px">LASTING ENERGY</span>
    <span class="forest" style="font-size:20px;font-weight:500;margin-top:2px">PAST MIDLIFE</span>
    <span class="rose" style="font-size:20px;font-weight:500;margin-top:6px">ZERO GYM NEEDED</span>
  </div>
</section>

<section class="tile col-1 row-3">
  <div class="photo tone-kitchen" style="top:0;height:160px" role="img" aria-label="Smiling woman in a white cropped sweater standing in a kitchen"></div>
  <svg class="overlay" viewBox="0 0 217 272" preserveAspectRatio="none" aria-hidden="true">
    <polygon points="0,145 217,157 217,272 0,272" fill="var(--blush-deep)"/>
  </svg>
  <div class="caption" style="top:164px">
    <span class="forest" style="font-size:34px;font-weight:600">TEN-WEEK</span>
    <span class="forest" style="font-size:26px;font-weight:600;margin-top:2px">BRIGHT MORNING</span>
    <span style="margin-top:6px"><span class="tag tag-rose" style="font-size:22px;font-weight:500">REBOOT</span></span>
  </div>
</section>

<section class="tile col-2 row-3">
  <div class="photo tone-produce" style="top:110px;height:162px" role="img" aria-label="Fresh produce framing a notepad menu on dark wood"></div>
  <svg class="overlay" viewBox="0 0 217 272" preserveAspectRatio="none" aria-hidden="true">
    <polygon points="0,0 217,0 217,117 0,126" fill="var(--rose)"/>
  </svg>
  <div class="caption" style="top:14px">
    <span class="white" style="font-size:32px;font-weight:500">QUICK GARDEN</span>
    <span class="white" style="font-size:32px;font-weight:500;margin-top:2px">KITCHEN</span>
    <span style="margin-top:3px"><span class="tag tag-forest" style="font-size:22px;font-weight:500">MENU GUIDE</span></span>
  </div>
</section>

<section class="tile col-3 row-3">
  <div class="photo tone-light" style="top:0;height:160px" role="img" aria-label="Woman whispering a secret to a surprised friend"></div>
  <svg class="overlay" viewBox="0 0 217 272" preserveAspectRatio="none" aria-hidden="true">
    <polygon points="0,150 217,160 217,272 0,272" fill="var(--blush-deep)"/>
  </svg>
  <div class="caption" style="top:166px">
    <span class="forest" style="font-size:20px;font-weight:500">STUDIO HABITS FOR</span>
    <span class="forest" style="font-size:20px;font-weight:500;margin-top:2px">LASTING ENERGY</span>
    <span class="forest" style="font-size:20px;font-weight:500;margin-top:2px">PAST MIDLIFE</span>
    <span style="margin-top:6px"><span class="tag tag-rose" style="font-size:20px;font-weight:500;padding:3px 12px">ZERO GYM NEEDED</span></span>
  </div>
</section>

</body>
</html>
```